Whitcombe Business Card Design

The name of the business is Dario Whitcombe, CPA LLC
The service that we offer is Accounting, Tax & Consulting Services. I need it to have the following items:
Dario Whitcombe, Principal
Phone Number
Email Address
Physical Address

I have attached the company logo, one in black and one in white. Please provide a design in black background and the other in white background. Please include "Accounting, Tax & Consulting Services". I want the business card to be clean and very professional.

```html
<!DOCTYPE html>
<html lang="en">
<head>
<meta charset="utf-8">
<title>Dario Whitcombe, CPA LLC — Business Card</title>
<link href="https://fonts.googleapis.com/css2?family=Montserrat:wght@600;700&family=Roboto:wght@300;400&display=swap" rel="stylesheet">
<style>
  :root {
    --backdrop: #2a2a2a;
    --card: #ececec;
    --ink: #333436;
    --grey: #76787b;
    --bar-grey: #8e8f92;
    --red: #8c1619;
    --body: #3a3a3a;
  }
  * { margin: 0; padding: 0; box-sizing: border-box; }
  html, body { width: 1200px; height: 1138px; overflow: hidden; }
  body { background: var(--backdrop); position: relative; font-family: "Roboto", sans-serif; }

  .card {
    position: absolute;
    background: var(--card);
    border-radius: 16px;
    overflow: hidden;
  }
  .card--front { left: 272px; top: 184px; width: 622px; height: 376px; }
  .card--back { left: 274px; top: 606px; width: 619px; height: 375px; }

  .mark-square { position: absolute; background: var(--ink); }
  .card--front .mark-square { left: 281px; top: 110px; width: 60px; height: 60px; }
  .card--back .mark-square { left: 508px; top: 54px; width: 60px; height: 60px; }

  .firm-name {
    position: absolute;
    font-family: "Montserrat", sans-serif;
    font-weight: 600;
    color: var(--ink);
    white-space: nowrap;
  }
  .firm-tagline {
    position: absolute;
    font-family: "Montserrat", sans-serif;
    font-weight: 600;
    color: var(--grey);
    white-space: nowrap;
  }
  .card--front .firm-name { left: 0; width: 100%; text-align: center; top: 192px; font-size: 25px; }
  .card--front .firm-tagline { left: 0; width: 100%; text-align: center; top: 229px; font-size: 18px; letter-spacing: 1.6px; }
  .card--back .firm-name { left: 28px; top: 54px; font-size: 22px; }
  .card--back .firm-tagline { left: 28px; top: 84px; font-size: 16px; letter-spacing: 1.4px; }

  .services {
    position: absolute;
    font-size: 16px;
    color: var(--body);
    white-space: nowrap;
  }
  .card--front .services { left: 0; width: 100%; text-align: center; top: 326px; }

  .front-bar { position: absolute; left: 0; bottom: 0; width: 100%; height: 10px; display: flex; }
  .front-bar__red { flex: 1; background: var(--red); }
  .front-bar__grey { flex: 1; background: var(--bar-grey); }

  .person-name {
    position: absolute; left: 28px; top: 156px;
    font-family: "Montserrat", sans-serif; font-weight: 700;
    font-size: 21px; color: var(--red); letter-spacing: 0.5px;
  }
  .person-role { position: absolute; left: 28px; top: 183px; font-size: 17px; font-weight: 300; color: var(--body); }

  .contacts { position: absolute; left: 28px; top: 226px; list-style: none; }
  .contacts li { display: flex; align-items: center; height: 24px; font-size: 16.5px; font-weight: 300; color: var(--body); }
  .contacts svg { width: 14px; height: 14px; margin-right: 12px; fill: var(--red); flex: none; }

  .address { position: absolute; left: 28px; top: 304px; font-size: 16.5px; font-weight: 300; color: var(--body); line-height: 23.5px; font-style: normal; }

  .services-band { position: absolute; left: 246px; top: 328px; width: 373px; height: 47px; }
  .services-band svg { position: absolute; inset: 0; }
  .card--back .services { left: 60px; top: 15px; color: #fff; font-weight: 300; font-size: 16.5px; }
</style>
</head>
<body>
  <section class="card card--front">
    <div class="mark-square"></div>
    <div class="firm-name">DARIO WHITCOMBE, CPA LLC</div>
    <div class="firm-tagline">CERTIFIED PUBLIC ACCOUNTANT</div>
    <div class="services">Accounting, Tax &amp; Consulting Services</div>
    <div class="front-bar"><span class="front-bar__red"></span><span class="front-bar__grey"></span></div>
  </section>

  <section class="card card--back">
    <div class="firm-name">DARIO WHITCOMBE, CPA LLC</div>
    <div class="firm-tagline">CERTIFIED PUBLIC ACCOUNTANT</div>
    <div class="mark-square"></div>

    <div class="person-name">DARIO WHITCOMBE</div>
    <div class="person-role">Principal</div>

    <ul class="contacts">
      <li><svg viewBox="0 0 16 16"><path d="M1 6c0-3 3-4 7-4s7 1 7 4l-3 1-1-2H5L4 7 1 6zM4 8h8l2 6H2l2-6zm4 1.5a2 2 0 100 4 2 2 0 000-4z"/></svg>555-204-7390</li>
      <li><svg viewBox="0 0 16 16"><path d="M1 3h14v10H1zM2.5 4.5 8 9l5.5-4.5v1L8 10 2.5 5.5z" fill-rule="evenodd"/></svg>dw@whitcombecpa.com</li>
      <li><svg viewBox="0 0 16 16"><path d="M8 1a7 7 0 100 14A7 7 0 008 1zm0 1.5c.9 0 1.8 1.8 2 4.5H6c.2-2.7 1.1-4.5 2-4.5zM2.6 7h2.4c0-1.7.4-3.2.9-4.2A5.6 5.6 0 002.6 7zm8.4 0h2.4a5.6 5.6 0 00-3.3-4.2c.5 1 .9 2.5.9 4.2zM2.6 9a5.6 5.6 0 003.3 4.2c-.5-1-.9-2.5-.9-4.2zm3.4 0c.2 2.7 1.1 4.5 2 4.5s1.8-1.8 2-4.5zm5 0c0 1.7-.4 3.2-.9 4.2A5.6 5.6 0 0013.4 9z"/></svg>www.whitcombecpa.com</li>
    </ul>

    <address class="address">4870, Larkspur Avenue, Fair<br>Hollow, US 204518</address>

    <div class="services-band">
      <svg viewBox="0 0 373 47" preserveAspectRatio="none"><path d="M24 0H373V47H0z" fill="var(--red)"/></svg>
      <div class="services">Accounting, Tax &amp; Consulting Services</div>
    </div>
  </section>
</body>
</html>
```